WordPress Site That Reviews Footwear

We need a wordpress web design for an affiliate site called PaceKite. We review and do roundups on footwear products. The final design should be clean and mobile friendly. The site should be built with Gutenberg page builder. We like the design of https://lunavessel.com/.
Updates

Need extra days to review

Target Market(s)

USA

Industry/Entity Type

Footwear

Logo Text

PaceKite

Number of Pages Required

4 page

Font styles to use
Serif
Sans Serif

Requirements
Must have
• Wordpress site
Blog post
Page
Categories
Homepage

```html
<!DOCTYPE html>
<html lang="en">
<head>
<meta charset="utf-8">
<title>PaceKite – Footwear Reviews</title>
<link rel="stylesheet" href="https://fonts.googleapis.com/css2?family=Libre+Caslon+Text:wght@400;700&family=Heebo:wght@400;500;700&family=Fira+Sans:wght@500&family=Poppins:wght@600&display=swap">
<style>
:root{
  --orange:#fd5c2a;
  --ink:#111111;
  --text:#2b2b2b;
  --muted:#f2f2f2;
  --white:#ffffff;
  --green:#3f8a1c;
  --star:#f7921e;
  --footer:#000000;
}
*{margin:0;padding:0;box-sizing:border-box}
html,body{width:1200px;height:3541px;overflow:hidden;background:var(--white)}
body{font-family:"Heebo",sans-serif;color:var(--text)}
.page{position:relative;width:1200px;height:3541px;overflow:hidden}
.abs{position:absolute}
.serif{font-family:"Libre Caslon Text",serif;font-weight:700;text-transform:uppercase;color:var(--ink)}
.rule{position:absolute;height:4px;width:63px;background:var(--orange)}

/* header */
.site-header{position:absolute;left:0;top:0;width:1200px;height:63px;background:var(--white)}
.nav-link{position:absolute;top:25px;font-size:11.5px;font-weight:700;letter-spacing:.3px;color:var(--ink)}
.brand{position:absolute;left:0;width:1190px;top:14px;text-align:center;font-family:"Libre Caslon Text",serif;font-size:30px;letter-spacing:1px;color:var(--ink)}
.head-icon{position:absolute;top:24px}

/* hero */
.hero{position:absolute;left:0;top:63px;width:1200px;height:587px;background:linear-gradient(180deg,#3a2a22 0%,#7a4f35 22%,#8a5a3c 50%,#7a4f35 78%,#2c211c 100%)}
.hero-title{position:absolute;left:0;width:1200px;top:180px;text-align:center;font-size:41px;line-height:58px;color:var(--white);letter-spacing:.5px}
.hero-sub{position:absolute;left:0;width:1200px;top:309px;text-align:center;font-size:15px;font-weight:500;color:var(--white)}
.btn{position:absolute;background:var(--orange);color:var(--white);border-radius:24px;font-family:"Libre Caslon Text",serif;font-weight:700;text-transform:uppercase;text-align:center}
.dots{position:absolute;top:559px;left:566px;display:flex;gap:4px}
.dots span{width:10px;height:10px;border-radius:50%;background:var(--white)}
.dots span.on{background:var(--orange)}

/* about */
.about-photo{position:absolute;left:93px;top:737px;width:449px;height:440px;background:linear-gradient(160deg,#f3c9b4,#e9b5a0 55%,#d9a892)}
.about-title{position:absolute;left:600px;top:738px;font-size:32px}
.about-text{position:absolute;left:600px;top:812px;width:492px;font-size:13.6px;line-height:30px;color:var(--text)}

/* benefits */
.benefit-panel{position:absolute;left:0;top:1311px;width:738px;height:557px;background:var(--orange)}
.benefit{position:absolute;width:300px}
.benefit .num{position:absolute;left:0;top:0;width:56px;height:56px;border-radius:50%;background:var(--white);color:var(--orange);font-family:"Heebo",sans-serif;font-weight:700;font-size:24px;text-align:center;line-height:56px}
.benefit h3{position:absolute;left:68px;top:-30px;font-family:"Libre Caslon Text",serif;font-size:16px;color:var(--white);text-transform:uppercase;white-space:nowrap}
.benefit p{position:absolute;left:68px;top:-4px;width:240px;font-size:13px;line-height:30px;color:var(--white)}
.benefits-title{position:absolute;left:738px;width:430px;top:1338px;text-align:center;font-size:33px}
.benefit-photo{position:absolute;left:720px;top:1416px;width:480px;height:397px;background:linear-gradient(180deg,#bdbdbd 0%,#d9d1cf 30%,#8d8a96 60%,#3c4a63 100%)}
.play{position:absolute;left:1100px;top:1708px;width:68px;height:68px;border-radius:50%;background:rgba(253,92,42,.35)}
.play i{position:absolute;left:8px;top:8px;width:52px;height:52px;border-radius:50%;background:var(--orange)}

/* testimonials */
.testimonials{position:absolute;left:0;top:1868px;width:1200px;height:517px;background:var(--muted)}
.section-title{position:absolute;left:0;width:1200px;text-align:center;font-size:33px}
.card{position:absolute;top:182px;width:243px;height:243px;background:var(--white);box-shadow:0 0 6px rgba(0,0,0,.12)}
.card.faded{opacity:.45}
.card .avatar{position:absolute;left:14px;top:13px;width:52px;height:52px;border-radius:50%;background:linear-gradient(180deg,#7a8da0,#c7a287)}
.card .name{position:absolute;left:76px;top:28px;font-family:"Fira Sans",sans-serif;font-weight:500;font-size:17px;color:var(--green)}
.card p{position:absolute;left:14px;top:72px;width:224px;font-size:13px;line-height:30px;color:var(--text);white-space:nowrap;overflow:hidden}
.card .stars{position:absolute;left:14px;top:198px;font-size:13px;letter-spacing:2px;color:var(--star)}

/* blogs */
.blog{position:absolute;top:2546px;width:315px}
.blog .thumb{width:315px;height:209px}
.blog h3{margin:16px 9px 0;font-family:"Libre Caslon Text",serif;font-size:15px;line-height:30px;color:var(--ink);text-transform:uppercase}
.blog p{margin:4px 9px 0;font-size:13.5px;line-height:30px;color:var(--text)}

/* footer */
.site-footer{position:absolute;left:0;top:2999px;width:1200px;height:542px;background:var(--footer);color:var(--white)}
.mail-title{position:absolute;left:0;width:1200px;top:84px;text-align:center;font-size:33px;color:var(--white)}
.mail-form{position:absolute;left:293px;top:160px;width:640px;height:52px;border-radius:26px;background:var(--white);border:2px solid var(--orange)}
.mail-form span{position:absolute;left:45px;top:15px;font-size:14px;color:#aaa}
.mail-form b{position:absolute;right:2px;top:2px;width:152px;height:44px;border-radius:22px;background:var(--orange);color:var(--white);font-family:"Libre Caslon Text",serif;font-size:15px;text-align:center;line-height:44px}
.f-line{position:absolute;height:1px;background:#cfcfcf}
.f-brand{position:absolute;left:115px;top:316px;font-family:"Libre Caslon Text",serif;font-size:32px;color:var(--white)}
.social{position:absolute;top:367px;width:32px;height:32px;border-radius:50%;background:var(--orange)}
.f-head{position:absolute;top:283px;font-family:"Poppins",sans-serif;font-weight:600;font-size:16px}
.f-list{position:absolute;top:318px;list-style:none;font-size:14px;line-height:30.4px}
.f-list li::before{content:"»";margin-right:10px;font-weight:700}
.f-contact{position:absolute;left:819px;font-size:14px;line-height:30px;color:var(--white)}
.f-contact svg{position:absolute;left:13px;top:8px}
.f-contact span{display:block;padding-left:36px}
.copy{position:absolute;left:0;width:1200px;top:495px;text-align:center;font-size:14px}
</style>
</head>
<body>
<div class="page">

<header class="site-header">
  <span class="nav-link" style="left:107px">HOME</span>
  <span class="nav-link" style="left:177px">ABOUT US</span>
  <span class="nav-link" style="left:274px">PRODUCT</span>
  <div class="brand">PACEKITE</div>
  <span class="nav-link" style="left:803px">BLOGS</span>
  <span class="nav-link" style="left:878px">BENEFITS</span>
  <svg class="head-icon" style="left:1011px" width="12" height="13" viewBox="0 0 12 13"><circle cx="6" cy="3.5" r="3" fill="#111"/><path d="M0 13c0-4 2.5-6 6-6s6 2 6 6z" fill="#111"/></svg>
  <svg class="head-icon" style="left:1043px" width="13" height="13" viewBox="0 0 13 13"><circle cx="5.2" cy="5.2" r="4" fill="none" stroke="#111" stroke-width="2"/><path d="M8 8l4 4" stroke="#111" stroke-width="2.2"/></svg>
  <svg class="head-icon" style="left:1076px" width="14" height="13" viewBox="0 0 14 13"><path d="M0 1h2.5l2 7h7.5l2-5.5H4" fill="none" stroke="#111" stroke-width="1.8"/><path d="M4 3h9l-1.5 5H5.5z" fill="#111"/><circle cx="5.5" cy="11" r="1.4" fill="#111"/><circle cx="11" cy="11" r="1.4" fill="#111"/></svg>
</header>

<section class="hero" role="img" aria-label="Rows of shoes laid out on a wooden floor">
  <h1 class="hero-title serif" style="color:var(--white)">Lorem ipsum dolor sit amet con<br>tetur adipiscing elit sed</h1>
  <p class="hero-sub">LOREM IPSUM DOLOR SIT AMET, CONSECTETUR ADIPISCING ELIT, SED DO EIUSMOD</p>
  <a class="btn" style="left:518px;top:356px;width:162px;height:47px;line-height:47px;font-size:15px">Get Started</a>
  <div class="dots"><span class="on"></span><span></span><span></span><span></span><span></span></div>
</section>

<section class="about">
  <div class="about-photo" role="img" aria-label="Woman trying on nude high heels"></div>
  <h2 class="about-title serif">About PaceKite</h2>
  <div class="rule" style="left:600px;top:786px"></div>
  <p class="about-text">Sed ut perspiciatis unde omnis iste natus error sit voluptatem accusantium doloremque laudantium, totam rem aperiam, eaque ipsa quae ab illo inven tore veritatis et quasi architecto beatae vitae dicta sunt explicabo. Nemo enim ipsam voluptatem quia voluptas sit aspernatur aut odit aut fugit, sed quia consequuntur magni dolores eos qui ratione voluptatem sequi nesci unt. Neque porro quisquam est, qui dolorem ipsum quia dolor sit amet, consectetur, adipisci velit, sed quia non numquam eius modi tempora incid unt ut labore et dolore magnam aliquam quaerat voluptatem. Ut enim ad minima veniam, quis nostrum exercitationem ullam corporis suscipit laboriosam, nisi ut aliquid ex ea commodi consequatu.</p>
  <a class="btn" style="left:600px;top:1124px;width:162px;height:47px;line-height:47px;font-size:15px">Learn More</a>
</section>

<section class="benefits">
  <div class="benefit-panel"></div>
  <div class="benefit" style="left:56px;top:1396px"><div class="num">1</div><h3>Lorem Ipsum</h3><p>Lorem ipsum dolor sit amet, consec tetur adipiscing elit, sed do eiusmod tempor incididunt ut labore.</p></div>
  <div class="benefit" style="left:391px;top:1396px"><div class="num">2</div><h3>Lorem Ipsum</h3><p>Lorem ipsum dolor sit amet, consec tetur adipiscing elit, sed do eiusmod tempor incididunt ut labore.</p></div>
  <div class="benefit" style="left:56px;top:1535px"><div class="num">3</div><h3>Lorem Ipsum</h3><p>Lorem ipsum dolor sit amet, consec tetur adipiscing elit, sed do eiusmod tempor incididunt ut labore.</p></div>
  <div class="benefit" style="left:391px;top:1535px"><div class="num">4</div><h3>Lorem Ipsum</h3><p>Lorem ipsum dolor sit amet, consec tetur adipiscing elit, sed do eiusmod tempor incididunt ut labore.</p></div>
  <div class="benefit" style="left:56px;top:1681px"><div class="num">5</div><h3>Lorem Ipsum</h3><p>Lorem ipsum dolor sit amet, consec tetur adipiscing elit, sed do eiusmod tempor incididunt ut labore.</p></div>
  <div class="benefit" style="left:391px;top:1681px"><div class="num">6</div><h3>Lorem Ipsum</h3><p>Lorem ipsum dolor sit amet, consec tetur adipiscing elit, sed do eiusmod tempor incididunt ut labore.</p></div>
  <h2 class="benefits-title serif">Our Benefits</h2>
  <div class="rule" style="left:832px;top:1390px"></div>
  <div class="benefit-photo" role="img" aria-label="Shoe rack with heels and sneakers on white shelves"></div>
  <div class="play"><i></i><svg class="abs" style="left:26px;top:23px" width="20" height="22" viewBox="0 0 20 22"><path d="M2 1l17 10L2 21z" fill="#fff"/></svg></div>
</section>

<section class="testimonials">
  <h2 class="section-title serif" style="top:84px">Our Client Testimonials</h2>
  <div class="rule" style="left:568px;top:134px"></div>
  <div class="card faded" style="left:-45px"><div class="avatar" role="img" aria-label="Client portrait"></div><div class="name">John Deo</div><p>Lorem ipsum dolor sit amet, conse<br>ctetur adipiscing elit, sed do eius<br>mod tempor incididunt ut labore et<br>dolore magna aliqua.</p><div class="stars">★★★★★</div></div>
  <div class="card" style="left:216px"><div class="avatar" role="img" aria-label="Client portrait"></div><div class="name">John Deo</div><p>Lorem ipsum dolor sit amet, conse<br>ctetur adipiscing elit, sed do eius<br>mod tempor incididunt ut labore et<br>dolore magna aliqua.</p><div class="stars">★★★★★</div></div>
  <div class="card" style="left:478px"><div class="avatar" role="img" aria-label="Client portrait"></div><div class="name">John Deo</div><p>Lorem ipsum dolor sit amet, conse<br>ctetur adipiscing elit, sed do eius<br>mod tempor incididunt ut labore et<br>dolore magna aliqua.</p><div class="stars">★★★★★</div></div>
  <div class="card" style="left:740px"><div class="avatar" role="img" aria-label="Client portrait"></div><div class="name">John Deo</div><p>Lorem ipsum dolor sit amet, conse<br>ctetur adipiscing elit, sed do eius<br>mod tempor incididunt ut labore et<br>dolore magna aliqua.</p><div class="stars">★★★★★</div></div>
  <div class="card faded" style="left:1002px"><div class="avatar" role="img" aria-label="Client portrait"></div><div class="name">John Deo</div><p>Lorem ipsum dolor sit amet, conse<br>ctetur adipiscing elit, sed do eius<br>mod tempor incididunt ut labore et<br>dolore magna aliqua.</p><div class="stars">★★★★★</div></div>
</section>

<section class="blogs">
  <h2 class="section-title serif" style="top:2463px">Our Latest Blogs</h2>
  <div class="rule" style="left:568px;top:2512px"></div>
  <article class="blog" style="left:111px"><div class="thumb" role="img" aria-label="Pairs of brown leather loafers" style="background:linear-gradient(135deg,#2a1a12,#8a5a38 55%,#5a3a28)"></div><h3>Lorem ipsum dolor sit amet, consectetur adipiscing</h3><p>Lorem ipsum dolor sit amet, consectetur adip iscing elit, sed do eiusmod tempor incididunt ut labore et dolore magna aliqua.</p></article>
  <article class="blog" style="left:443px"><div class="thumb" role="img" aria-label="Leather boot stepping over metal nails" style="background:linear-gradient(180deg,#1c1c1c,#4a3428 55%,#8c8a86)"></div><h3>Lorem ipsum dolor sit amet, consectetur adipiscing</h3><p>Lorem ipsum dolor sit amet, consectetur adip iscing elit, sed do eiusmod tempor incididunt ut labore et dolore magna aliqua.</p></article>
  <article class="blog" style="left:773px"><div class="thumb" role="img" aria-label="Runner tying pink sneakers on a mat" style="background:linear-gradient(135deg,#c9c6c0,#8f8a86 50%,#d6909a)"></div><h3>Lorem ipsum dolor sit amet, consectetur adipiscing</h3><p>Lorem ipsum dolor sit amet, consectetur adip iscing elit, sed do eiusmod tempor incididunt ut labore et dolore magna aliqua.</p></article>
</section>

<footer class="site-footer">
  <h2 class="mail-title serif" style="color:var(--white)">Join Our Mailing List</h2>
  <div class="mail-form"><span>Enter Email Here</span><b>SUBSCRIBE</b></div>
  <div class="f-line" style="left:111px;top:245px;width:976px"></div>

  <div class="f-brand">PACEKITE</div>
  <span class="social" style="left:113px"></span>
  <span class="social" style="left:160px"></span>
  <span class="social" style="left:208px"></span>
  <span class="social" style="left:255px"></span>

  <div class="f-head" style="left:367px">QUICK LINKS</div>
  <ul class="f-list" style="left:378px"><li>Home</li><li>Product</li><li>Why Choose Us</li><li>Benefits</li></ul>
  <div class="f-head" style="left:584px">LEGAL</div>
  <ul class="f-list" style="left:589px"><li>Privacy Policy</li><li>Terms &amp; Conditions</li><li>Contact Us</li><li>About Us</li></ul>
  <div class="f-head" style="left:819px">CONTACT US</div>
  <div class="f-contact" style="top:318px"><svg width="10" height="14" viewBox="0 0 10 14"><path d="M5 0a5 5 0 0 0-5 5c0 4 5 9 5 9s5-5 5-9a5 5 0 0 0-5-5z" fill="#fff"/><circle cx="5" cy="5" r="1.8" fill="#000"/></svg><span>123 Sed ut perspiciatis unde omnis<br>iste natus error sit voluptatem</span></div>
  <div class="f-contact" style="top:380px"><svg width="13" height="13" viewBox="0 0 13 13"><path d="M3 0l2.2 3-1.4 1.6a8 8 0 0 0 4.6 4.6L10 7.8 13 10l-1.4 2.6C6 13 0 7 .4 1.4z" fill="#fff"/></svg><span>123 456 7890</span></div>
  <div class="f-contact" style="top:423px"><svg width="15" height="11" viewBox="0 0 15 11"><rect width="15" height="11" fill="#fff"/><path d="M0 0l7.5 6L15 0" fill="none" stroke="#000" stroke-width="1.3"/></svg><span style="padding-left:40px">hello@pacekite.com</span></div>

  <div class="f-line" style="left:74px;top:473px;width:1052px"></div>
  <p class="copy">© Copyright 2021 &nbsp;<b>PACEKITE</b> &nbsp; | &nbsp;&nbsp; All Rights Reserved</p>
</footer>

</div>
</body>
</html>
```